Boundless Volt Product design

We need a bottle design for our product. Boundless Volt is a Gaming Nootropic made to increase Energy, Focus, Reaction time, and Clarity of an eSport gamer. It will be 40 servings a bottle. Currently, all the ingredients haven't been finalized so after the competition is over we will have to work with the designer to also make an ingredients label for the back of it. For the flavor, we will call it tundra mist.

The attachments included:. The velvet outlaws picture as a font style I like for the logo.
The Z CHARGE REFRESH PICTURE IS WHAT WE WANT OUR DESIGN to look like something similar a clean and simple design that stands out!

Z Charge bottle is what our biggest competitors product looks like. The boundless volt picture as the current logo we are using but can be changed.

Overall the pictures are just some references for what I could possibly want the design to look like however, I'm open to your designer's ideas and concepts you think would make for a cool looking Gaming Nootropic product bottle design. I appreciate everyone working on this and look forward to seeing your designs have a great day!

Target Market(s)

Gamers between the ages of 18-30

Industry/Entity Type

Health And Wellness

Requirements
Must have
• Boundless Volt logo, state that it is for energy, focus, reaction, and clarity. state 40 serivngs. state flavor.

```html
<!DOCTYPE html>
<html lang="en">
<head>
<meta charset="utf-8">
<title>Boundless Volt – Tundra Mist Label</title>
<link rel="stylesheet" href="https://fonts.googleapis.com/css2?family=Roboto+Condensed:ital,wght@0,700;1,500;1,700&display=swap">
<style>
  :root {
    --page-bg: #f7f7f8;
    --label-edge: #e3e6ea;
    --brand-blue: #1a67b5;
    --brand-blue-deep: #1557a0;
    --band-blue: rgba(27, 104, 190, 0.88);
    --ice-light: #e9f3fb;
    --ice-mid: #8fcdf0;
    --ice-deep: #3f9fe0;
    --haze: #e4e6ef;
    --white: #ffffff;
  }
  * { margin: 0; padding: 0; box-sizing: border-box; }
  html, body {
    width: 1200px;
    height: 1200px;
    overflow: hidden;
    background: var(--page-bg);
  }
  .label {
    position: absolute;
    left: 70px;
    top: 451px;
    width: 1060px;
    height: 299px;
    overflow: hidden;
    border: 1px solid var(--label-edge);
    font-family: "Roboto Condensed", "Arial Narrow", sans-serif;
  }
  .ice-scene {
    position: absolute;
    inset: 0;
    background:
      radial-gradient(ellipse 260px 26px at 50% 34%, rgba(255,255,255,0.95), rgba(255,255,255,0) 100%),
      radial-gradient(ellipse 220px 150px at 50% 30%, rgba(255,255,255,0.9), rgba(255,255,255,0) 100%),
      radial-gradient(ellipse 300px 200px at 14% 80%, var(--ice-deep), rgba(63,159,224,0) 70%),
      radial-gradient(ellipse 300px 220px at 86% 70%, var(--ice-deep), rgba(63,159,224,0) 70%),
      linear-gradient(180deg, var(--haze) 0%, var(--ice-light) 22%, var(--ice-mid) 55%, var(--ice-deep) 100%);
  }
  .brand-lockup {
    position: absolute;
    left: 0;
    right: 0;
    top: 82px;
    display: flex;
    justify-content: center;
    align-items: center;
    gap: 10px;
    color: var(--brand-blue);
    font-weight: 700;
    font-size: 24px;
    letter-spacing: 0.5px;
  }
  .brand-dot {
    width: 22px;
    height: 22px;
    border-radius: 50%;
    background: var(--brand-blue);
  }
  .flavor-name {
    position: absolute;
    left: 0;
    right: 0;
    top: 136px;
    text-align: center;
    color: var(--brand-blue);
    font-style: italic;
    font-weight: 700;
    font-size: 44px;
    line-height: 1;
    letter-spacing: 0.3px;
  }
  .benefits {
    position: absolute;
    left: 0;
    right: 0;
    top: 205px;
    text-align: center;
    color: var(--brand-blue-deep);
    font-style: italic;
    font-weight: 500;
    font-size: 19px;
    line-height: 1;
  }
  .benefits .sep { margin: 0 4px; }
  .info-band {
    position: absolute;
    left: 0;
    right: 0;
    bottom: 0;
    height: 44px;
    background: var(--band-blue);
    color: var(--white);
  }
  .band-brand {
    position: absolute;
    left: 36px;
    top: 14px;
    display: flex;
    align-items: center;
    gap: 6px;
    font-weight: 700;
    font-size: 13px;
    letter-spacing: 0.3px;
    text-transform: uppercase;
  }
  .band-brand .brand-dot {
    width: 14px;
    height: 14px;
    background: var(--white);
  }
  .servings {
    position: absolute;
    left: 0;
    right: 0;
    top: 13px;
    text-align: center;
    font-style: italic;
    font-weight: 500;
    font-size: 13px;
  }
</style>
</head>
<body>
  <div class="label">
    <div class="ice-scene" role="img" aria-label="Photographic backdrop of blue glacier ice blocks and frost crystals with a bright light flare"></div>

    <div class="brand-lockup">
      <span class="brand-dot"></span>
      <span class="brand-name">BOUNDLESS VOLT</span>
    </div>

    <h1 class="flavor-name">TUNDRA MIST</h1>

    <p class="benefits">energy <span class="sep">•</span> focus <span class="sep">•</span> reaction <span class="sep">•</span> clarity</p>

    <div class="info-band">
      <div class="band-brand">
        <span class="brand-dot"></span>
        <span>Boundless Volt</span>
      </div>
      <p class="servings">40 serivngs</p>
    </div>
  </div>
</body>
</html>
```